Business card - mobile service

O KiraLink is a mobile family safety service based on tablets and smartphones.
The business card must have:
BASIC INFO
Company Logo
Name
Position / Job Title: Co-founder
Mobile Phone Number: +55 (11) 5080 6192
Land Line: +55 (11) 8765 093412
Email Address: name@kiralink-example.com
Web Site URL: www.kiralink-example.com
PROMOTIONAL INFO
Try KiraLink free Today!
Your personal promo code: qqqq-5151-hhhh-3030-9876
Promo code text explanation with the instructions about the trial offer
Updates
Dears,
One more must have: the KiraLink slogan:
Industry/Entity Type
Safety
Look and feel
Each slider illustrates characteristics of the customer's brand and the style your logo design should communicate.

```html
<!DOCTYPE html>
<html lang="en">
<head>
<meta charset="utf-8">
<title>KiraLink business card</title>
<link rel="stylesheet" href="https://fonts.googleapis.com/css2?family=Arimo:wght@400;700&display=swap">
<style>
  :root {
    --page-bg: #3a3a3a;
    --card-white: #ffffff;
    --brand-blue: #1ba3dd;
    --brand-blue-light: #5cc5ef;
    --ink-dark: #2b2b2b;
    --ink-grey: #777777;
    --on-blue: #ffffff;
  }
  * { box-sizing: border-box; margin: 0; padding: 0; }
  html, body { width: 1200px; height: 900px; overflow: hidden; }
  body {
    background: var(--page-bg);
    font-family: "Arimo", Arial, sans-serif;
    position: relative;
  }
  .card {
    position: absolute;
    left: 210px;
    width: 678px;
    background: var(--card-white);
    border-radius: 22px;
    overflow: hidden;
  }

  /* Front: promotional side */
  .card-front { top: 27px; height: 401px; }
  .band {
    position: absolute; left: 0; right: 0;
    background: linear-gradient(180deg, var(--brand-blue) 0%, var(--brand-blue-light) 100%);
  }
  .band-top { top: 0; height: 104px; }
  .band-bottom {
    top: 272px; bottom: 0;
    background: linear-gradient(0deg, var(--brand-blue) 0%, var(--brand-blue-light) 100%);
  }
  .front-slogan {
    position: absolute; top: 36px; left: 0; right: 0;
    text-align: center; color: var(--on-blue);
    font-weight: 700; font-size: 28px;
  }
  .front-wordmark {
    position: absolute; top: 128px; left: 0; right: 0;
    display: flex; justify-content: center; align-items: center; gap: 18px;
    color: var(--brand-blue); font-weight: 700; font-size: 104px; letter-spacing: -2px;
  }
  .wordmark-dot {
    width: 34px; height: 34px; border-radius: 50%;
    background: var(--brand-blue);
  }
  .front-offer {
    position: absolute; top: 293px; left: 0; right: 0;
    text-align: center; color: var(--on-blue);
    font-weight: 700; font-size: 28px;
  }
  .front-promo {
    position: absolute; top: 334px; left: 0; right: 0;
    text-align: center; color: var(--on-blue);
    font-size: 19px; letter-spacing: 0.5px;
  }
  .front-terms {
    position: absolute; top: 367px; left: 0; right: 0;
    text-align: center; color: var(--on-blue);
    font-size: 11px;
  }

  /* Back: contact side */
  .card-back { top: 477px; height: 375px; }
  .back-wordmark {
    position: absolute; top: 30px; left: 0; right: 0;
    display: flex; justify-content: center; align-items: center; gap: 8px;
    color: var(--brand-blue); font-weight: 700; font-size: 54px; letter-spacing: -1px;
  }
  .back-wordmark .wordmark-dot { width: 16px; height: 16px; }
  .back-slogan {
    position: absolute; top: 92px; left: 0; right: 0;
    text-align: center; color: var(--brand-blue);
    font-weight: 700; font-size: 20px;
  }
  .person {
    position: absolute; top: 193px; left: 455px; width: 180px;
    text-align: center;
  }
  .person-name { color: var(--brand-blue); font-size: 23px; }
  .person-title { color: var(--ink-grey); font-size: 15px; margin-top: 4px; }
  .contact-list {
    position: absolute; left: 30px; top: 252px;
    list-style: none;
  }
  .contact-item {
    display: flex; align-items: center; gap: 12px;
    height: 27px;
    color: var(--ink-dark); font-size: 15px; letter-spacing: 0.3px;
  }
  .contact-icon { width: 20px; height: 20px; flex: none; }
</style>
</head>
<body>

<section class="card card-front" aria-label="Promotional side">
  <div class="band band-top"></div>
  <div class="band band-bottom"></div>
  <p class="front-slogan">Your Family Safety Service</p>
  <div class="front-wordmark"><span>KiraLink</span><span class="wordmark-dot"></span></div>
  <p class="front-offer">Try KiraLink free Today!</p>
  <p class="front-promo">Your personal promo code: qqqq-5151-hhhh-3030-9876</p>
  <p class="front-terms">Promo code text explanation with the instructions about the trial offer</p>
</section>

<section class="card card-back" aria-label="Contact side">
  <div class="back-wordmark"><span>KiraLink</span><span class="wordmark-dot"></span></div>
  <p class="back-slogan">Your Family Safety Service</p>
  <div class="person">
    <p class="person-name">Your Name Here</p>
    <p class="person-title">Co-founder</p>
  </div>
  <ul class="contact-list">
    <li class="contact-item">
      <svg class="contact-icon" viewBox="0 0 20 20" aria-hidden="true"><path d="M2 8 C2 4 18 4 18 8 L15 9 L14 7 H6 L5 9 Z M5 10 H15 L17 16 H3 Z" fill="var(--brand-blue)"/><circle cx="10" cy="13" r="2" fill="#fff"/></svg>
      <span>+55 (11) 8765 093412</span>
    </li>
    <li class="contact-item">
      <svg class="contact-icon" viewBox="0 0 20 20" aria-hidden="true"><rect x="6" y="1" width="8" height="18" rx="2" fill="var(--brand-blue)"/><rect x="7.5" y="4" width="5" height="8" fill="#fff"/></svg>
      <span>+55 (11) 5080 6192</span>
    </li>
    <li class="contact-item">
      <svg class="contact-icon" viewBox="0 0 20 20" aria-hidden="true"><rect x="1" y="4" width="18" height="12" rx="2" fill="var(--brand-blue)"/><path d="M2 5 L10 11 L18 5" stroke="#fff" stroke-width="1.2" fill="none"/></svg>
      <span>name@kiralink-example.com</span>
    </li>
    <li class="contact-item">
      <svg class="contact-icon" viewBox="0 0 20 20" aria-hidden="true"><circle cx="10" cy="10" r="9" fill="none" stroke="var(--brand-blue)" stroke-width="2"/><ellipse cx="10" cy="10" rx="4" ry="8" fill="none" stroke="var(--brand-blue)" stroke-width="1.4"/><path d="M2 10 H18" stroke="var(--brand-blue)" stroke-width="1.4"/></svg>
      <span>www.kiralink-example.com</span>
    </li>
  </ul>
</section>

</body>
</html>
```